Velora Entertainment

Logo for business card design

Target Market(s)

potential film investors and screenwriters

Industry/Entity Type

Business

Contact Information for Business Card

as shown, website here is a placeholder position

Requirements
Must have
• great visual appeal
Nice to have
• harmony of colors; must evoke spirit of
• U.S.-China cooperation

```html
<!DOCTYPE html>
<html lang="en">
<head>
<meta charset="utf-8">
<title>Velora Entertainment – Business Card</title>
<link rel="stylesheet" href="https://fonts.googleapis.com/css2?family=Open+Sans:ital,wght@0,400;0,600;1,700&display=swap">
<style>
  :root {
    --backdrop: #4a4a4a;
    --card: #ffffff;
    --brand-red: #e0141e;
    --brand-blue: #16168a;
    --band-gray: #9d9d9d;
    --ink: #1b1b1b;
    --rule: #d6d6d6;
  }
  * { box-sizing: border-box; margin: 0; padding: 0; }
  html, body {
    width: 1105px; height: 1200px; overflow: hidden;
    background: var(--backdrop);
    font-family: "Open Sans", Arial, sans-serif;
  }
  .business-card {
    position: absolute; left: 50px; top: 314px;
    width: 1005px; height: 572px;
    background: var(--card);
    overflow: hidden;
  }
  .brand-mark {
    position: absolute; left: 123px; top: 190px; width: 360px;
    display: flex; align-items: center; gap: 18px;
  }
  .brand-square { width: 54px; height: 54px; background: var(--brand-red); flex: none; }
  .brand-name {
    color: var(--brand-blue); font-weight: 600; font-size: 38px; line-height: 1.12;
  }
  .divider {
    position: absolute; left: 520px; top: 117px; width: 2px; height: 295px;
    background: var(--rule);
  }
  .contact { position: absolute; left: 574px; top: 112px; color: var(--ink); }
  .person-name { color: var(--brand-red); font-weight: 600; font-size: 33px; line-height: 40px; }
  .person-title { color: var(--brand-blue); font-size: 27px; line-height: 34px; }
  .address { margin-top: 30px; font-size: 26px; line-height: 35px; }
  .lines { margin-top: 15px; list-style: none; }
  .lines li {
    display: flex; align-items: center; gap: 14px;
    font-size: 26px; line-height: 38px; margin-left: 2px;
  }
  .lines svg { width: 22px; height: 22px; flex: none; fill: var(--brand-red); }
  .footer-band {
    position: absolute; left: 0; bottom: 0; width: 1005px; height: 62px;
    background: var(--band-gray);
    display: flex; align-items: center; justify-content: flex-end;
    padding-right: 86px;
  }
  .website {
    font-weight: 700; font-style: italic; font-size: 24px;
    letter-spacing: 3px; color: var(--ink);
  }
</style>
</head>
<body>
  <div class="business-card">
    <div class="brand-mark">
      <span class="brand-square"></span>
      <span class="brand-name">Velora<br>Entertainment</span>
    </div>

    <div class="divider"></div>

    <div class="contact">
      <h1 class="person-name">Daniel Hart</h1>
      <p class="person-title">CEO/Founder</p>
      <p class="address">2140 Larkspur Court<br>Anchorage, Alaska 34610</p>
      <ul class="lines">
        <li>
          <svg viewBox="0 0 24 24" aria-hidden="true"><path d="M6.6 10.8a15.1 15.1 0 0 0 6.6 6.6l2.2-2.2c.3-.3.7-.4 1-.2 1.1.4 2.3.6 3.6.6.6 0 1 .4 1 1V20c0 .6-.4 1-1 1A17 17 0 0 1 3 4c0-.6.4-1 1-1h3.5c.6 0 1 .4 1 1 0 1.3.2 2.5.6 3.6.1.3 0 .7-.2 1z"/></svg>
          555 204 7319
        </li>
        <li>
          <svg viewBox="0 0 24 24" aria-hidden="true"><path d="M7 1h10a2 2 0 0 1 2 2v18a2 2 0 0 1-2 2H7a2 2 0 0 1-2-2V3a2 2 0 0 1 2-2zm0 3v14h10V4zm5 15.5a1.2 1.2 0 1 0 0 2.4 1.2 1.2 0 0 0 0-2.4z"/></svg>
          555 318 6042
        </li>
        <li>
          <svg viewBox="0 0 24 24" aria-hidden="true"><path d="M2 5h20v2l-10 6L2 7zm0 4 10 6 10-6v10H2z"/></svg>
          hello@veloraent.com
        </li>
      </ul>
    </div>

    <div class="footer-band">
      <p class="website">www.veloraent.com</p>
    </div>
  </div>
</body>
</html>
```